VelvetLine Dating Plattform Design Proposal

Layout Proposal
HTML or PSD

Dating Platform, where young ladies (f.e. students) are looking for generous man that support them. In return they will spend time with the sugar daddies (dining, cinema, exhibitions, romantic rendez-vous).

Page consist out of 2 pages
1. Primary landing page
2. Detail page for each profile

1. Primary Landing Page
a. Headline: Hier suchen JUNGE FRAUEN, den REIFEN MANN der weiss wie zu verwöhnen!
b. Subtitle/Explanation (can be positioned on top of profiles or at side): Viele junge Frauen können nichts mit den Männern in ihrem Alter anfangen oder sie lieben einfach die Möglichkeiten die ihnen ein reiferer Mann bieten kann. Auf Velvetline bieten wir den jungen Damen dafür eine Kontaktmöglichkeit. Sie inserieren auf Velvetline privat und sind keine profesionellen.
c. List of Profiles with pictures, description text, name and number
2. Detail Page
a. Picture of Profile
b. Description Text
c. Additional blurred pictures
d. Field to enter email to see pictures unblurred

Example pages:
- http://lumo-abendrunde.ch/

Design:
- Feel free for your suggestions of look’n’feel. Keep in mind that we address generous man
- The way how profiles (20 -30 total) shall be listed on Page 1 is up to you (list, carroussel, slider,..)
- As well feel free to add any background pics/aminations

Attached find Excel with profiles and ZIP with pictures

Industry/Entity Type

Dating

Number of Pages Required

2 page

Requirements
Must have
• Page consist out of 2 pages
• 1. Primary landing page
• 2. Detail page for each profile
• 1. Primary Landing Page
• a. Headline: Hier suchen JUNGE FRAUEN, den REIFEN MANN der weiss wie zu verwöhnen!
• b. Subtitle/Explanation (can be positioned on top of profiles or at side): Viele junge Frauen können nichts mit den Männern in ihrem Alter anfangen oder sie lieben einfach die Möglichkeiten die ihnen ein reiferer Mann bieten kann. Auf Velvetline bieten wir den jungen Damen dafür eine Kontaktmöglichkeit. Sie inserieren auf Velvetline privat und sind keine profesionellen.
• c. List of Profiles with pictures, description text, name and number
• 2. Detail Page
• a. Picture of Profile
• b. Description Text
• c. Additional blurred pictures
• d. Field to enter email to see pictures unblurred

```html
<!DOCTYPE html>
<html lang="de">
<head>
<meta charset="utf-8">
<title>VelvetLine – Dating Plattform</title>
<link rel="stylesheet" href="https://fonts.googleapis.com/css2?family=Roboto:wght@300;400;500;700&display=swap">
<style>
:root{
  --magenta:#c8409c;
  --magenta-dark:#a8317f;
  --ink:#333;
  --text:#555;
  --muted:#777;
  --line:#e4e4e4;
  --card-bg:#f7f7f7;
  --button:#5d5d5d;
  --button-dark:#3c3c3c;
  --white:#fff;
}
*{box-sizing:border-box;margin:0;padding:0}
html,body{width:1200px;height:2691px;overflow:hidden}
body{font-family:"Roboto",Arial,sans-serif;color:var(--text);background:var(--white);position:relative}

/* top bar */
.topbar{height:34px;background:var(--magenta);color:var(--white);font-size:13px;display:flex;justify-content:flex-end;align-items:center;gap:34px;padding-right:38px}
.topbar span{display:flex;align-items:center;gap:8px}
.topbar svg{width:11px;height:11px;fill:var(--white)}

/* header */
.site-header{height:86px;position:relative;border-bottom:3px solid var(--magenta)}
.logo{position:absolute;left:99px;top:16px;font-size:42px;font-weight:500;color:var(--magenta);letter-spacing:-.5px}
.main-nav{position:absolute;left:492px;top:0;display:flex;height:64px}
.main-nav a{font-size:13px;color:var(--ink);text-decoration:none;display:flex;align-items:center;padding:0 18px;text-transform:uppercase;margin-right:15px}
.main-nav a.active{background:var(--magenta);color:var(--white);border-radius:0 0 8px 8px;padding:0 16px}
.search{position:absolute;left:906px;top:27px;width:194px;height:32px;border:1px solid #d8d8d8;display:flex;align-items:center;justify-content:space-between;padding:0 10px;font-size:11px;color:#888}
.search svg{width:11px;height:11px}

/* hero */
.hero{height:577px;position:relative;display:flex}
.hero-photo{height:100%}
.hero-photo.one{width:339px;background:linear-gradient(160deg,#8a6a4f,#b99b77 45%,#6b4a36)}
.hero-photo.two{width:425px;background:linear-gradient(180deg,#e9e7e9,#cfc9cf 55%,#a8a0a8)}
.hero-photo.three{width:436px;background:linear-gradient(200deg,#7a5e86,#a07c8e 50%,#c4a7a4)}
.hero-title{position:absolute;left:341px;top:178px;width:423px;height:169px;background:rgba(45,45,45,.78);color:var(--white);font-size:27px;line-height:36px;text-align:center;display:flex;align-items:center;justify-content:center;padding:0 20px}
.hero-arrow{position:absolute;top:310px;width:46px;height:74px;background:rgba(40,40,40,.75);display:flex;align-items:center;justify-content:center}
.hero-arrow.prev{left:0;border-radius:0 40px 40px 0}
.hero-arrow.next{right:0;border-radius:40px 0 0 40px}
.hero-arrow svg{width:18px;height:22px;fill:var(--white)}

/* welcome panel */
.welcome{position:relative;margin:-101px auto 0;width:1001px;height:388px;background:linear-gradient(90deg,rgba(255,255,255,.93),rgba(252,244,249,.9));border:1px solid var(--line);display:flex}
.welcome-main{width:696px;position:relative;border-right:1px solid var(--line)}
.welcome-title{position:absolute;left:0;top:0;width:398px;height:54px;background:var(--magenta);color:var(--white);font-size:24px;line-height:54px;padding-left:20px;clip-path:polygon(0 0,92% 0,100% 100%,0 100%)}
.welcome-photo{position:absolute;left:19px;top:104px;width:280px;height:225px;border:2px solid #555;background:linear-gradient(150deg,#d9d4d6,#8e8488 55%,#2e2a2c)}
.welcome-text{position:absolute;left:326px;top:96px;width:345px;font-size:11.5px;line-height:20px;color:var(--muted)}
.welcome-text p{margin-bottom:12px}
.more-link{position:absolute;left:326px;top:312px;font-size:14px;color:var(--muted);display:flex;align-items:center;gap:8px;text-transform:uppercase}
.more-link svg{width:14px;height:14px}
.day-girl{flex:1;text-align:center;position:relative}
.day-girl h2{font-size:23px;font-weight:400;color:var(--ink);height:54px;line-height:54px;border-bottom:1px solid #e8c6dc}
.day-girl .avatar{width:158px;height:158px;border-radius:50%;border:3px solid var(--magenta);margin:20px auto 0;background:linear-gradient(170deg,#6d6258,#c9ae7e 60%,#e2d3b4)}
.day-girl .name{font-style:italic;font-size:15px;color:var(--ink);margin-top:20px}
.day-girl .blurb{font-size:11.5px;line-height:20px;color:var(--muted);width:250px;margin:10px auto 0}
.day-girl .age{font-style:italic;font-size:15px;color:var(--ink);margin-top:12px}

/* profiles */
.profiles{width:1001px;margin:57px auto 0;display:grid;grid-template-columns:repeat(4,232px);column-gap:25px;row-gap:37px}
.profile-card{height:431px;background:var(--card-bg);border:1px solid var(--line);display:flex;flex-direction:column}
.card-head{height:41px;display:flex;justify-content:space-between;align-items:center;padding:0 12px 0 16px;background:var(--white)}
.card-head .name{font-size:14px;color:var(--ink);text-transform:uppercase}
.card-head .phone{font-size:16px;color:var(--magenta)}
.card-photo{height:168px}
.card-info{padding:18px 16px 0;font-size:12px;line-height:24px;color:var(--text);flex:1}
.card-info .desc{font-size:11px;line-height:17px;color:var(--muted);margin-top:10px}
.card-button{height:32px;background:var(--button);color:var(--white);font-size:12px;display:flex;align-items:center;justify-content:space-between;padding:0 18px}
.card-button svg{width:12px;height:12px}

/* subscribe */
.subscribe{position:absolute;left:0;top:2480px;width:1200px;height:100px;background:var(--magenta);color:var(--white)}
.subscribe .envelope{position:absolute;left:78px;top:18px;width:96px;height:70px;opacity:.28}
.subscribe .plane{position:absolute;left:196px;top:36px;width:40px;height:34px}
.subscribe .label{position:absolute;left:251px;top:28px;font-size:16px;font-weight:500;line-height:22px;text-transform:uppercase}
.subscribe form{position:absolute;left:567px;top:30px;display:flex;height:41px}
.subscribe .field{width:375px;background:var(--white);border-radius:21px 0 0 21px;font-size:12px;color:#777;display:flex;align-items:center;padding-left:22px}
.subscribe .send{width:127px;background:var(--button-dark);border-radius:0 21px 21px 0;font-size:13px;font-weight:500;display:flex;align-items:center;justify-content:center}

/* footer */
.site-footer{position:absolute;left:0;top:2580px;width:1200px;height:111px;text-align:center}
.footer-nav{margin-top:35px;font-size:11px;color:var(--ink);text-transform:uppercase}
.footer-nav span.sep{margin:0 10px;color:#999}
.copyright{margin-top:12px;font-size:11.5px;color:var(--ink)}
</style>
</head>
<body>

<div class="topbar">
  <span>Call Us: +1 800 555 0142</span>
  <span><svg viewBox="0 0 10 10"><rect x="1.5" y="4.5" width="7" height="5" rx=".6"/><path d="M3 4.5V3a2 2 0 0 1 4 0v1.5" fill="none" stroke="#fff" stroke-width="1.2"/></svg>Sign In</span>
  <span><svg viewBox="0 0 10 10"><circle cx="5" cy="3" r="2.3"/><path d="M.8 10a4.2 4.2 0 0 1 8.4 0z"/></svg>Registered</span>
</div>

<header class="site-header">
  <div class="logo">VelvetLine</div>
  <nav class="main-nav">
    <a class="active" href="#">Home</a>
    <a href="#">About Us</a>
    <a href="#">Profile</a>
    <a href="#">Contact Us</a>
  </nav>
  <div class="search">Search item
    <svg viewBox="0 0 12 12"><circle cx="5" cy="5" r="3.6" fill="none" stroke="#333" stroke-width="1.6"/><path d="M7.7 7.7 11 11" stroke="#333" stroke-width="1.8"/></svg>
  </div>
</header>

<section class="hero">
  <div class="hero-photo one" role="img" aria-label="Foto einer jungen Frau auf einem Korbsessel"></div>
  <div class="hero-photo two" role="img" aria-label="Foto einer jungen Frau in hellem Raum"></div>
  <div class="hero-photo three" role="img" aria-label="Foto einer jungen Frau in blauem Top"></div>
  <h1 class="hero-title" style="font-weight:400">Hier suchen JUNGE FRAUEN, den REIFEN MANN der weiss wie zu verwöhnen!</h1>
  <div class="hero-arrow prev"><svg viewBox="0 0 18 22"><path d="M14 2 5 11l9 9" fill="none" stroke="#fff" stroke-width="3.5"/></svg></div>
  <div class="hero-arrow next"><svg viewBox="0 0 18 22"><path d="m4 2 9 9-9 9" fill="none" stroke="#fff" stroke-width="3.5"/></svg></div>
</section>

<section class="welcome">
  <div class="welcome-main">
    <h2 class="welcome-title" style="font-weight:400">Welcome To VelvetLine</h2>
    <div class="welcome-photo" role="img" aria-label="Foto einer jungen Frau auf weissen Kissen"></div>
    <div class="welcome-text">
      <p>Viele junge Frauen können nichts mit den Männern in ihrem Alter anfangen oder sie lieben einfach die Möglichkeiten die ihnen ein reiferer Mann bieten kann. Auf Velvetline bieten wir den jungen Damen dafür eine Kontaktmöglichkeit. Sie inserieren auf Velvetline privat und sind keine profesionellen.</p>
      <p>Sed ut perspiciatis unde omnis iste natus error sit voluptatem accusantium doloremque laudantium, totam rem aperiam, eaque ipsa quae ab illo inventore veritatis et quasi architecto beatae vitae dicta sunt explicabo. Nemo enim ipsam</p>
    </div>
    <div class="more-link">More Information
      <svg viewBox="0 0 14 14"><circle cx="7" cy="7" r="7" fill="#555"/><path d="m5.5 4 3 3-3 3" fill="none" stroke="#fff" stroke-width="1.6"/></svg>
    </div>
  </div>
  <aside class="day-girl">
    <h2>Girl Des Tages</h2>
    <div class="avatar" role="img" aria-label="Profilfoto des Girls des Tages"></div>
    <div class="name">Lena Marquardt</div>
    <p class="blurb">Lorem ipsum dolor sit amet, consectetur adipiscing elit, sed do eiusmod tempor incididunt ut labore et dolore</p>
    <div class="age">Age : 22</div>
  </aside>
</section>

<main class="profiles">
  <article class="profile-card">
    <div class="card-head"><span class="name">Becky</span><span class="phone">+1 800 555 0142</span></div>
    <div class="card-photo" role="img" aria-label="Profilfoto Becky" style="background:linear-gradient(160deg,#4a3a38,#9a7466 55%,#c9b07a)"></div>
    <div class="card-info">Age &nbsp;: 21<br>Weight &nbsp;: 58<br>Height : 5 feet and 4 inches
      <p class="desc">Neque porro quisquam est, qui dolorem ipsum quia dolor sit amet, consectetur, adipisci velit, sed quia non numquam eius modi tempora incidunt ut labore</p></div>
    <div class="card-button">VIEW PROFILE <svg viewBox="0 0 12 12"><circle cx="6" cy="6" r="6" fill="#fff"/><path d="m5 3.5 2.5 2.5L5 8.5" fill="none" stroke="#5d5d5d" stroke-width="1.5"/></svg></div>
  </article>
  <article class="profile-card">
    <div class="card-head"><span class="name">Brenda</span><span class="phone">+1 800 555 0142</span></div>
    <div class="card-photo" role="img" aria-label="Profilfoto Brenda" style="background:linear-gradient(150deg,#e8e6e6,#6a5a55 50%,#1e1a1a)"></div>
    <div class="card-info">Age &nbsp;: 21<br>Weight &nbsp;: 58<br>Height : 5 feet and 4 inches
      <p class="desc">Neque porro quisquam est, qui dolorem ipsum quia dolor sit amet, consectetur, adipisci velit, sed quia non numquam eius modi tempora incidunt ut labore</p></div>
    <div class="card-button">VIEW PROFILE <svg viewBox="0 0 12 12"><circle cx="6" cy="6" r="6" fill="#fff"/><path d="m5 3.5 2.5 2.5L5 8.5" fill="none" stroke="#5d5d5d" stroke-width="1.5"/></svg></div>
  </article>
  <article class="profile-card">
    <div class="card-head"><span class="name">Carla</span><span class="phone">+1 800 555 0142</span></div>
    <div class="card-photo" role="img" aria-label="Profilfoto Carla" style="background:linear-gradient(170deg,#7a5c4a,#d59a86 50%,#e7a7c4)"></div>
    <div class="card-info">Age &nbsp;: 21<br>Weight &nbsp;: 58<br>Height : 5 feet and 4 inches
      <p class="desc">Neque porro quisquam est, qui dolorem ipsum quia dolor sit amet, consectetur, adipisci velit, sed quia non numquam eius modi tempora incidunt ut labore</p></div>
    <div class="card-button">VIEW PROFILE <svg viewBox="0 0 12 12"><circle cx="6" cy="6" r="6" fill="#fff"/><path d="m5 3.5 2.5 2.5L5 8.5" fill="none" stroke="#5d5d5d" stroke-width="1.5"/></svg></div>
  </article>
  <article class="profile-card">
    <div class="card-head"><span class="name">Celine</span><span class="phone">+1 800 555 0142</span></div>
    <div class="card-photo" role="img" aria-label="Profilfoto Celine" style="background:linear-gradient(160deg,#8d7662,#c8a48a 50%,#b9b2b3)"></div>
    <div class="card-info">Age &nbsp;: 21<br>Weight &nbsp;: 58<br>Height : 5 feet and 4 inches
      <p class="desc">Neque porro quisquam est, qui dolorem ipsum quia dolor sit amet, consectetur, adipisci velit, sed quia non numquam eius modi tempora incidunt ut labore</p></div>
    <div class="card-button">VIEW PROFILE <svg viewBox="0 0 12 12"><circle cx="6" cy="6" r="6" fill="#fff"/><path d="m5 3.5 2.5 2.5L5 8.5" fill="none" stroke="#5d5d5d" stroke-width="1.5"/></svg></div>
  </article>

  <article class="profile-card">
    <div class="card-head"><span class="name">Emilia</span><span class="phone">+1 800 555 0142</span></div>
    <div class="card-photo" role="img" aria-label="Profilfoto Emilia" style="background:linear-gradient(160deg,#8a6a4f,#c0a07c 50%,#5e4636)"></div>
    <div class="card-info">Age &nbsp;: 21<br>Weight &nbsp;: 58<br>Height : 5 feet and 4 inches
      <p class="desc">Neque porro quisquam est, qui dolorem ipsum quia dolor sit amet, consectetur, adipisci velit, sed quia non numquam eius modi tempora incidunt ut labore</p></div>
    <div class="card-button">VIEW PROFILE <svg viewBox="0 0 12 12"><circle cx="6" cy="6" r="6" fill="#fff"/><path d="m5 3.5 2.5 2.5L5 8.5" fill="none" stroke="#5d5d5d" stroke-width="1.5"/></svg></div>
  </article>
  <article class="profile-card">
    <div class="card-head"><span class="name">Gina</span><span class="phone">+1 800 555 0142</span></div>
    <div class="card-photo" role="img" aria-label="Profilfoto Gina" style="background:linear-gradient(150deg,#c9803e,#7a5a3c 50%,#2e2622)"></div>
    <div class="card-info">Age &nbsp;: 21<br>Weight &nbsp;: 58<br>Height : 5 feet and 4 inches
      <p class="desc">Neque porro quisquam est, qui dolorem ipsum quia dolor sit amet, consectetur, adipisci velit, sed quia non numquam eius modi tempora incidunt ut labore</p></div>
    <div class="card-button">VIEW PROFILE <svg viewBox="0 0 12 12"><circle cx="6" cy="6" r="6" fill="#fff"/><path d="m5 3.5 2.5 2.5L5 8.5" fill="none" stroke="#5d5d5d" stroke-width="1.5"/></svg></div>
  </article>
  <article class="profile-card">
    <div class="card-head"><span class="name">Lara</span><span class="phone">+1 800 555 0142</span></div>
    <div class="card-photo" role="img" aria-label="Profilfoto Lara" style="background:linear-gradient(160deg,#d8d2c8,#9a8474 50%,#6a5548)"></div>
    <div class="card-info">Age &nbsp;: 21<br>Weight &nbsp;: 58<br>Height : 5 feet and 4 inches
      <p class="desc">Neque porro quisquam est, qui dolorem ipsum quia dolor sit amet, consectetur, adipisci velit, sed quia non numquam eius modi tempora incidunt ut labore</p></div>
    <div class="card-button">VIEW PROFILE <svg viewBox="0 0 12 12"><circle cx="6" cy="6" r="6" fill="#fff"/><path d="m5 3.5 2.5 2.5L5 8.5" fill="none" stroke="#5d5d5d" stroke-width="1.5"/></svg></div>
  </article>
  <article class="profile-card">
    <div class="card-head"><span class="name">Loraine</span><span class="phone">+1 800 555 0142</span></div>
    <div class="card-photo" role="img" aria-label="Profilfoto Loraine" style="background:linear-gradient(170deg,#8f8466,#d9c7a4 50%,#c9a3a0)"></div>
    <div class="card-info">Age &nbsp;: 21<br>Weight &nbsp;: 58<br>Height : 5 feet and 4 inches
      <p class="desc">Neque porro quisquam est, qui dolorem ipsum quia dolor sit amet, consectetur, adipisci velit, sed quia non numquam eius modi tempora incidunt ut labore</p></div>
    <div class="card-button">VIEW PROFILE <svg viewBox="0 0 12 12"><circle cx="6" cy="6" r="6" fill="#fff"/><path d="m5 3.5 2.5 2.5L5 8.5" fill="none" stroke="#5d5d5d" stroke-width="1.5"/></svg></div>
  </article>

  <article class="profile-card">
    <div class="card-head"><span class="name">Marion</span><span class="phone">+1 800 555 0142</span></div>
    <div class="card-photo" role="img" aria-label="Profilfoto Marion" style="background:linear-gradient(170deg,#4a3a3a,#a98070 45%,#2fa6cf)"></div>
    <div class="card-info">Age &nbsp;: 21<br>Weight &nbsp;: 58<br>Height : 5 feet and 4 inches
      <p class="desc">Neque porro quisquam est, qui dolorem ipsum quia dolor sit amet, consectetur, adipisci velit, sed quia non numquam eius modi tempora incidunt ut labore</p></div>
    <div class="card-button">VIEW PROFILE <svg viewBox="0 0 12 12"><circle cx="6" cy="6" r="6" fill="#fff"/><path d="m5 3.5 2.5 2.5L5 8.5" fill="none" stroke="#5d5d5d" stroke-width="1.5"/></svg></div>
  </article>
  <article class="profile-card">
    <div class="card-head"><span class="name">Sara</span><span class="phone">+1 800 555 0142</span></div>
    <div class="card-photo" role="img" aria-label="Profilfoto Sara" style="background:linear-gradient(160deg,#2a2220,#b88a5e 50%,#3a2a22)"></div>
    <div class="card-info">Age &nbsp;: 21<br>Weight &nbsp;: 58<br>Height : 5 feet and 4 inches
      <p class="desc">Neque porro quisquam est, qui dolorem ipsum quia dolor sit amet, consectetur, adipisci velit, sed quia non numquam eius modi tempora incidunt ut labore</p></div>
    <div class="card-button">VIEW PROFILE <svg viewBox="0 0 12 12"><circle cx="6" cy="6" r="6" fill="#fff"/><path d="m5 3.5 2.5 2.5L5 8.5" fill="none" stroke="#5d5d5d" stroke-width="1.5"/></svg></div>
  </article>
  <article class="profile-card">
    <div class="card-head"><span class="name">Suze</span><span class="phone">+1 800 555 0142</span></div>
    <div class="card-photo" role="img" aria-label="Profilfoto Suze" style="background:linear-gradient(160deg,#b8523e,#c07a68 50%,#9a4c5c)"></div>
    <div class="card-info">Age &nbsp;: 21<br>Weight &nbsp;: 58<br>Height : 5 feet and 4 inches
      <p class="desc">Neque porro quisquam est, qui dolorem ipsum quia dolor sit amet, consectetur, adipisci velit, sed quia non numquam eius modi tempora incidunt ut labore</p></div>
    <div class="card-button">VIEW PROFILE <svg viewBox="0 0 12 12"><circle cx="6" cy="6" r="6" fill="#fff"/><path d="m5 3.5 2.5 2.5L5 8.5" fill="none" stroke="#5d5d5d" stroke-width="1.5"/></svg></div>
  </article>
  <article class="profile-card">
    <div class="card-head"><span class="name">Vanja</span><span class="phone">+1 800 555 0142</span></div>
    <div class="card-photo" role="img" aria-label="Profilfoto Vanja" style="background:linear-gradient(160deg,#5a3e34,#b08a78 50%,#2c2220)"></div>
    <div class="card-info">Age &nbsp;: 21<br>Weight &nbsp;: 58<br>Height : 5 feet and 4 inches
      <p class="desc">Neque porro quisquam est, qui dolorem ipsum quia dolor sit amet, consectetur, adipisci velit, sed quia non numquam eius modi tempora incidunt ut labore</p></div>
    <div class="card-button">VIEW PROFILE <svg viewBox="0 0 12 12"><circle cx="6" cy="6" r="6" fill="#fff"/><path d="m5 3.5 2.5 2.5L5 8.5" fill="none" stroke="#5d5d5d" stroke-width="1.5"/></svg></div>
  </article>
</main>

<section class="subscribe">
  <svg class="envelope" viewBox="0 0 96 70"><g fill="none" stroke="#fff" stroke-width="4"><rect x="6" y="8" width="84" height="56" rx="4" transform="rotate(-10 48 36)"/><path d="m10 16 38 26 40-30" transform="rotate(-10 48 36)"/></g></svg>
  <svg class="plane" viewBox="0 0 40 34"><path d="M2 16 38 2 30 32 19 22 14 30 13 20z" fill="none" stroke="#fff" stroke-width="2.4" stroke-linejoin="round"/><path d="M13 20 38 2" stroke="#fff" stroke-width="2"/></svg>
  <div class="label">Subscribe to receive updates and<br>exclusive offers.</div>
  <form>
    <div class="field">Enter your E - mail</div>
    <div class="send">SUBSCRIBE</div>
  </form>
</section>

<footer class="site-footer">
  <nav class="footer-nav">Home<span class="sep">/</span>List of Profiles<span class="sep">/</span>About Us<span class="sep">/</span>Checking<span class="sep">/</span>Community<span class="sep">/</span>Contact Us</nav>
  <p class="copyright">2016 © Copyrights VelvetLine.All Rights Reserved</p>
</footer>

</body>
</html>
```